Legal Journal cover - modern and sylish

We require a cover design for a new, modern and digital legal academic journal. Attached is our logo so you can get an idea of the feel. This academic journal will have several editions per year.Requirements for the cover design:-The feel of the cover is to be modern -In harmony with our logo-While staying uniform and set in its design,

Colors
ec1f27

Requirements
Must have
• 1) Colour. Each edition will use different colours. (So we will need the source files to be able to continue to do this)
• 2) An image section. We would like to be able to put in different image or photo with each edition. So we need to have a section, most likely in the shape of a strip, that can include a different image or photo each edition. This part is where we can put a different image in for each edition. So this section would need to be able to accommodate different types of images. It could be a single square. Or it could be a line (a strip) that an image or images.
• 3) A title for the edition and volume and number. Like this:
• Volume 34, No 2 (2016): Contemporary Issues in Criminal Law
• I have attached a range of journals I found online to serve as inspiration.

```html
<!DOCTYPE html>
<html lang="en">
<head>
<meta charset="utf-8">
<title>Lex Forum – Legal &amp; Academic Journal, January 2020</title>
<link rel="stylesheet" href="https://fonts.googleapis.com/css2?family=Roboto:wght@400;500;700&display=swap">
<style>
  :root {
    --paper: #ffffff;
    --edition-green: #677a66;
    --numeral-green: #80907f;
    --mark-tint: #97a092;
    --brand-red: #ec1f27;
    --brand-grey: #6e6e6e;
    --photo-light: #a3a6aa;
    --photo-mid: #6d7079;
    --photo-dark: #4c4f5c;
    --type-light: #ffffff;
  }
  * { margin: 0; padding: 0; box-sizing: border-box; }
  html, body {
    width: 849px;
    height: 1200px;
    overflow: hidden;
    background: var(--paper);
    font-family: "Roboto", Arial, sans-serif;
  }
  .cover {
    position: relative;
    width: 849px;
    height: 1200px;
    background: var(--paper);
    overflow: hidden;
  }
  .edition-panel {
    position: absolute;
    left: 394px;
    top: 0;
    width: 455px;
    height: 1200px;
    background: var(--edition-green);
  }
  .edition-mark {
    position: absolute;
    left: 496px;
    top: 406px;
    width: 250px;
    height: 250px;
  }
  .edition-image {
    position: absolute;
    left: 0;
    top: 375px;
    width: 394px;
    height: 295px;
    background:
      linear-gradient(160deg, transparent 0 38%, rgba(76,79,92,0.55) 38% 62%, transparent 62%),
      linear-gradient(180deg, var(--photo-light) 0%, var(--photo-mid) 45%, var(--photo-dark) 70%, var(--photo-light) 100%);
  }
  .issue-number {
    position: absolute;
    left: 124px;
    top: 150px;
    font-weight: 500;
    font-size: 296px;
    line-height: 1;
    letter-spacing: -6px;
    color: var(--numeral-green);
    mix-blend-mode: multiply;
  }
  .brand {
    position: absolute;
    left: 173px;
    top: 893px;
    display: flex;
    align-items: center;
    gap: 10px;
  }
  .brand-dot {
    width: 62px;
    height: 62px;
    border-radius: 50%;
    background: var(--brand-grey);
  }
  .brand-name {
    color: var(--brand-red);
    font-weight: 500;
    font-size: 29px;
    line-height: 0.95;
    letter-spacing: 1px;
  }
  .title-marker {
    position: absolute;
    left: 394px;
    top: 907px;
    width: 24px;
    height: 24px;
    background: var(--brand-red);
  }
  .journal-title {
    position: absolute;
    left: 426px;
    top: 899px;
    color: var(--type-light);
    font-weight: 700;
    font-size: 32px;
    line-height: 1.2;
    white-space: nowrap;
    letter-spacing: -0.2px;
  }
  .edition-date {
    position: absolute;
    left: 428px;
    top: 955px;
    color: var(--type-light);
    font-weight: 400;
    font-size: 22px;
    line-height: 1.2;
  }
</style>
</head>
<body>
  <main class="cover">
    <div class="edition-panel"></div>
    <svg class="edition-mark" viewBox="0 0 250 250" aria-hidden="true">
      <circle cx="125" cy="125" r="125" fill="var(--mark-tint)" opacity="0.55"/>
    </svg>

    <div class="edition-image" role="img" aria-label="Edition photograph: architectural interior with hanging vertical rods over angled grey panels"></div>
    <div class="issue-number">01</div>

    <div class="brand">
      <span class="brand-dot"></span>
      <span class="brand-name">LEX<br>FORUM</span>
    </div>

    <div class="title-marker"></div>
    <h1 class="journal-title">Legal &amp; Academic Journal</h1>
    <p class="edition-date">January 2020</p>
  </main>
</body>
</html>
```